Laser Tattoo Removal Business Cards

We are looking for a professional business card design for a laser tattoo removal business. Ideally looking for a black business card design. The name of the business is Brightline Tattoo Removal. We place our cards at local tattoo shops so we ideally are looking for something trendy/edgy to draw both male and female clientele in.

Target Market(s)

Male/Female ages 18-60

Contact Information for Business Card

black background ideally.. hoping to stay within greys, whites and black

Font styles to use
Serif
Sans Serif

Colors
121212
a9a9a9
5c5c5c
f5f5f5
ffffff
7f7f7f
606060
848484
9d9d9d

Requirements
Must have
• Employee Info:
• Melissa Thornbury
• Chief Executive Offer
• m: 919.537.2846
• w: 919.362.4178
• f: 919.685.3907
• mthornbury@brightlinetattooremoval.example
• Address:
• 4615 Oakmere Pkwy, Suite 210
• Raleigh, NC 27654
• Website:
• www.brightlinetattooremoval.example
Nice to have
• Myabe business name on back or logo on back and employee info on the front

```html
<!DOCTYPE html>
<html lang="en">
<head>
<meta charset="utf-8">
<title>Brightline Tattoo Removal – Business Cards</title>
<link href="https://fonts.googleapis.com/css2?family=Roboto:wght@400;500&family=Roboto+Condensed:wght@500&display=swap" rel="stylesheet">
<style>
  :root{
    --bg:#d9d9d9;
    --card-black:#121212;
    --card-white:#f5f5f5;
    --white:#ffffff;
    --ink:#121212;
    --text:#5c5c5c;
    --muted:#848484;
    --rule:#7f7f7f;
    --tab:#121212;
  }
  *{margin:0;padding:0;box-sizing:border-box}
  html,body{width:1200px;height:960px;overflow:hidden}
  body{background:var(--bg);position:relative;font-family:"Roboto",Arial,sans-serif}

  .card{position:absolute;width:600px;height:342px;box-shadow:0 3px 8px rgba(0,0,0,.35)}
  .card--front{left:315px;top:113px;background:var(--card-white);color:var(--text)}
  .card--back{left:311px;top:472px;height:343px;background:var(--card-black);color:var(--white)}

  .brand-name{font-family:"Roboto Condensed","Arial Narrow",sans-serif;font-weight:500;text-transform:uppercase;letter-spacing:3px;line-height:1.15}
  .card--front .brand-name{position:absolute;left:32px;top:62px;width:240px;font-size:25px;color:var(--ink);text-align:center}
  .card--back .brand-name{position:absolute;left:0;right:0;top:112px;font-size:36px;color:var(--white);text-align:center}

  .holder{position:absolute;right:33px;top:183px;text-align:right}
  .holder__name{font-family:"Roboto Condensed","Arial Narrow",sans-serif;font-weight:500;font-size:21px;color:var(--ink);text-transform:uppercase;line-height:24px}
  .holder__title{font-size:15px;color:var(--muted);line-height:18px}
  .tab{position:absolute;right:1px;top:184px;width:10px;height:36px;background:var(--tab)}
  .rule{position:absolute;left:31px;top:231px;width:533px;height:2px;background:var(--rule)}

  .contact{position:absolute;left:31px;top:245px;list-style:none;font-size:12.5px;line-height:18.7px;white-space:nowrap}
  .contact li{display:flex;align-items:center;gap:8px}
  .contact svg{width:13px;height:13px;fill:var(--ink);flex:none}
  .address{position:absolute;right:33px;top:245px;text-align:right;font-size:12.5px;line-height:18.7px;font-style:normal;white-space:nowrap}

  .web-band{position:absolute;left:0;right:0;top:288px;height:27px;background:var(--white);color:var(--ink);text-align:center;font-size:14px;letter-spacing:2.6px;line-height:27px}
</style>
</head>
<body>
  <section class="card card--front" aria-label="Card front">
    <div class="brand-name">Brightline Tattoo Removal</div>
    <div class="holder">
      <div class="holder__name">Melissa Thornbury</div>
      <div class="holder__title">Chief Executive Offer</div>
    </div>
    <div class="tab"></div>
    <div class="rule"></div>
    <ul class="contact">
      <li><svg viewBox="0 0 24 24"><path d="M6.6 10.8a15 15 0 0 0 6.6 6.6l2.2-2.2c.3-.3.7-.4 1-.2 1.1.4 2.3.6 3.6.6.6 0 1 .4 1 1V20c0 .6-.4 1-1 1A17 17 0 0 1 3 4c0-.6.4-1 1-1h3.5c.6 0 1 .4 1 1 0 1.3.2 2.5.6 3.6.1.3 0 .7-.2 1z"/></svg>919.362.4178</li>
      <li><svg viewBox="0 0 24 24"><path d="M7 1h10a2 2 0 0 1 2 2v18a2 2 0 0 1-2 2H7a2 2 0 0 1-2-2V3a2 2 0 0 1 2-2zm0 3v14h10V4z"/></svg>919.537.2846</li>
      <li><svg viewBox="0 0 24 24"><path d="M6 2h12v5H6zM3 8h18a2 2 0 0 1 2 2v7h-4v5H5v-5H1v-7a2 2 0 0 1 2-2zm4 8v4h10v-4z"/></svg>919.685.3907</li>
      <li><svg viewBox="0 0 24 24"><path d="M2 5h20v14H2zm2 2v.5l8 5 8-5V7z"/></svg>mthornbury@brightlinetattooremoval.example</li>
    </ul>
    <address class="address">
      4615 Oakmere Pkwy<br>
      Suite 210<br>
      Raleigh, NC 27654<br>
      www.brightlinetattooremoval.example
    </address>
  </section>

  <section class="card card--back" aria-label="Card back">
    <div class="brand-name">Brightline<br>Tattoo Removal</div>
    <div class="web-band">www.brightlinetattooremoval.example</div>
  </section>
</body>
</html>
```